Online Dating Website called WinkAtWheel.com

PLEASE CAN ALL PARTICIPATING DESIGNERS PLEASE SUBMIT ALL PAGES AS DETAILED IN THE ORIGINAL BRIEF BELOW WITHIN 48 HOURS TO AVOID WINKATWHEEL EXTENDING THE CONTEST FURTHER.

We have an online dating website that is 95% fully functional and now require an exciting and creative designer to help us create the best dating experience. We are looking for your ideas on a couple of our key pages. These are our landing, profile and search page. We already have a homepage that we are happy with and winning designers will look to build upon the foundations of the homepage and extend them through their designs.

The premise of the site is the idea that if you've ever seen someone out driving and wished you could communicate because you found them attractive, how would you? Well with WinkAtWheel.com you can. Just enter their vehicle registration number (license plate) in to the website in order to get in touch, flirt and develop a relationship. It also allows users to find each other based on other criteria. It acts as both a specialist service and a normal dating website.

The pages that require developing are 1) our landing page, this is the page users see when they first login to the site, it comprises various pieces of information but it's primary function is a live feed of events generated based on the users favourited profiles and interactions with the user. 2) The profile page is the page where users can edit their own information, given the nature of this page we are looking for a creative design that gives this page some flair. 3) Finally we are looking for ideas for our search page, this page needs to provide a list of users who meet the user's search requirements and display the profile of a selected user.
Updates

Project Deadline Extended
Reason: We've asked for certain pages in our brief to be designed and this still hasn't been done. We've contacted the designers that have currently submitted designs and requested this several times. We still await for this to happen.

Target Market(s)

Male or Female age 18+

Industry/Entity Type

Dating

Requirements
Must have
• Our must have feature is a designer with an open mind. The functionality of the site must be present, all we ask is for you to be creative with the layout. Think out side of the box, change the colours, the layout, and the background as you feel. Make it look current and appealing to the user.
Nice to have
• Theme's carried through from the home page
Should not have
• Do not include Comic Sans or Times New Roman font in your designs.

```html
<!DOCTYPE html>
<html lang="en">
<head>
<meta charset="utf-8">
<title>winkatwheel – Home</title>
<link rel="stylesheet" href="https://fonts.googleapis.com/css2?family=Ubuntu:wght@300;400;500&display=swap">
<style>
:root{
  --navy:#0b3f66; --navy-dark:#062a47; --navy-pill:#04223a;
  --blue:#29a3dc; --blue-dark:#1682bf;
  --pink:#e94a97; --pink-dark:#d12c7c;
  --green:#6cbf1e; --green-dark:#4f9d10;
  --orange:#fba51a; --orange-dark:#f38a0a;
  --yellow:#f3b612;
  --ink:#333; --muted:#8d8d8d; --line:#e4e4e4; --card:#fff;
  --page:#fff; --footer:#262626; --footer-low:#1d1d1d; --cyan:#3cc4ea;
}
*{box-sizing:border-box;margin:0;padding:0}
html,body{width:705px;height:1200px;overflow:hidden;background:var(--page)}
body{font-family:"Ubuntu",Arial,sans-serif;color:var(--ink);position:relative}
.abs{position:absolute}

/* header */
.site-header{left:0;top:0;width:705px;height:65px;background:linear-gradient(#0f4f7c,var(--navy-dark))}
.brand{left:54px;top:20px;display:flex;align-items:center;gap:6px;color:#fff;font-size:19px;font-weight:400}
.brand-dot{width:14px;height:14px;border-radius:50%;background:var(--pink)}
.main-nav{left:254px;top:23px;display:flex;align-items:center;font-size:10.5px;color:#fff}
.main-nav a{color:#fff;text-decoration:none;padding:0 8px;border-right:1px solid rgba(255,255,255,.5);line-height:11px}
.main-nav a:last-child{border-right:0}
.main-nav a.active{background:var(--navy-pill);border-radius:12px;padding:6px 12px;border:0;margin-right:6px}

/* panels */
.panel{background:var(--card);border:1px solid var(--line);border-radius:5px;box-shadow:0 1px 2px rgba(0,0,0,.06);overflow:hidden}
.panel-head{height:24px;line-height:24px;padding-left:12px;color:#fff;font-size:11px;border-radius:4px 4px 0 0}
.head-blue{background:linear-gradient(var(--blue),var(--blue-dark))}
.head-green{background:linear-gradient(var(--green),var(--green-dark))}
.head-orange{background:linear-gradient(var(--orange),var(--orange-dark))}
.head-pink{background:linear-gradient(var(--pink),var(--pink-dark))}

/* life */
.life-photo{margin:8px auto 0;width:103px;height:57px;border-radius:6px;background:linear-gradient(135deg,#6b5a4a,#c7b8a4 60%,#4d4a47)}
.status-field{margin:7px 10px 0;height:15px;border:1px solid #d5d5d5;border-radius:8px;font-size:7px;color:#555;line-height:13px;padding-left:8px;position:relative}
.status-field .go{position:absolute;right:0;top:0;width:13px;height:13px;border-radius:50%;background:var(--pink)}
.status-field .go::after{content:"";position:absolute;left:5px;top:3.5px;border-left:4px solid #fff;border-top:3px solid transparent;border-bottom:3px solid transparent}
.life-actions{display:flex;gap:6px;margin:6px 0 0 13px}
.btn{font-size:7px;color:#fff;height:13px;line-height:13px;padding:0 10px;border-radius:2px}
.btn-navy{background:var(--navy)}
.btn-orange{background:var(--orange-dark)}

/* stats */
.stats{padding:10px 12px 0 14px;font-size:6.3px}
.stats h4{font-size:7.5px;font-weight:400;color:#333;margin:0 0 2px;line-height:10px}
.stats .row{display:flex;justify-content:space-between;color:var(--muted);line-height:12px;white-space:nowrap}
.stats .row span:first-child{overflow:hidden;text-overflow:clip;max-width:84px}
.stats .row span:last-child{width:12px;text-align:right;flex:none}
.stats .group{margin-bottom:10px}

/* favourites */
.person{display:flex;gap:7px;padding:6px 0 5px 12px;border-bottom:1px solid #efefef;margin:0 5px 0 0;height:53px}
.person:last-child{border-bottom:0}
.thumb{width:42px;height:42px;border-radius:5px;flex:none}
.person-info{font-size:6.5px;color:var(--muted);line-height:12px;padding-top:1px}
.person-info b{font-weight:500;color:#444;font-size:7px}

/* feed */
.post{left:186px;width:338px}
.post-head{height:27px;line-height:27px;border-radius:6px;color:#fff;font-size:11px;padding-left:12px;position:relative;z-index:1}
.post-body{margin:-3px 2px 0;height:71px;border:1px solid var(--line);border-top:0;border-radius:0 0 5px 5px;display:flex;padding:10px 0 0 14px;gap:9px;background:var(--card)}
.avatar{width:52px;height:52px;border-radius:8px;flex:none}
.post-text{font-size:7px;color:var(--muted);line-height:13px;font-weight:300}
.post-meta{display:flex;align-items:center;gap:5px;color:#444;font-weight:500;margin-top:3px}
.bubble{width:13px;height:8px;background:#444;border-radius:4px;position:relative}
.bubble::after{content:"";position:absolute;left:2px;bottom:-3px;border-top:4px solid #444;border-right:4px solid transparent}
.pager{left:188px;top:944px;width:340px;height:20px;background:#f1f1f1;border:1px solid var(--line);border-radius:3px;display:flex;align-items:center;justify-content:space-between;padding:0 14px 0 12px;font-size:7.5px;color:#555}
.pages{display:flex;gap:6px}
.pages span{width:11px;text-align:center}
.pages .current{background:#333;color:#fff;border-radius:2px}

/* right */
.beta{left:534px;top:79px;width:124px;height:76px;background:var(--yellow);border-radius:5px;color:#fff;padding:13px 12px}
.beta strong{display:block;font-size:13px;font-weight:400}
.beta span{font-size:9px;line-height:12px;display:block;margin-top:2px}
.match-list{list-style:none;padding:4px 14px 0 14px}
.match-list li{font-size:6.8px;color:var(--muted);border-bottom:1px solid #efefef;line-height:16px;white-space:nowrap;overflow:hidden}
.match-list li:last-child{border-bottom:0}
.tile-grid{display:grid;grid-template-columns:repeat(3,30px);gap:7px 8px;padding:9px 0 0 9px}
.tile{width:30px;height:30px;border-radius:6px}

/* footer */
.site-footer{left:0;top:992px;width:705px;height:208px;background:linear-gradient(#1a1a1a,var(--footer) 12%)}
.footer-col{top:26px}
.footer-col h3{font-size:13px;font-weight:400;color:var(--cyan);margin-bottom:6px}
.footer-col li{list-style:none;font-size:8px;font-weight:300;color:#e6e6e6;line-height:15px}
.divider{top:34px;width:1px;height:73px;background:#3a3a3a}
.social{display:flex;gap:6px;margin-top:2px}
.social span{width:15px;height:15px;border-radius:2px}
.footer-brand{left:549px;top:102px;color:#fff;font-size:16px;display:flex;align-items:center;gap:6px}
.footer-base{left:0;top:168px;width:705px;height:40px;background:var(--footer-low);font-size:7px;color:#777;padding:14px 0 0 58px}
</style>
</head>
<body>

<header class="site-header abs">
  <div class="brand abs">winkatwheel<span class="brand-dot"></span></div>
  <nav class="main-nav abs">
    <a class="active">Home</a><a>Profile</a><a>Messages</a><a>Matches</a><a>Search</a><a>Support</a><a>My Account</a>
  </nav>
</header>

<!-- left column -->
<section class="panel abs" style="left:49px;top:81px;width:124px;height:147px">
  <div class="panel-head head-blue">Life</div>
  <div class="life-photo" role="img" aria-label="Member profile photo"></div>
  <div class="status-field">how are you?<span class="go"></span></div>
  <div class="life-actions"><span class="btn btn-navy">Profile</span><span class="btn btn-orange">Upload</span></div>
</section>

<section class="panel abs" style="left:49px;top:234px;width:124px;height:190px">
  <div class="panel-head head-green">Seen Someone?</div>
  <div class="stats">
    <div class="group"><h4>LIKE 125</h4>
      <div class="row"><span>Praesent elementum elit</span><span>16</span></div>
      <div class="row"><span>Curabitur metus ipsum luctus</span><span>18</span></div>
      <div class="row"><span>Eu malesuada ut tincidunt se</span><span>20</span></div></div>
    <div class="group"><h4>MESSAGE 171</h4>
      <div class="row"><span>Praesent elementum elit</span><span>02</span></div>
      <div class="row"><span>Curabitur metus ipsum luctus</span><span>13</span></div></div>
    <div class="group"><h4>FAVOURITES 20</h4>
      <div class="row"><span>Praesent elementum elit</span><span>20</span></div>
      <div class="row"><span>Curabitur metus ipsum luctus</span><span>30</span></div></div>
  </div>
</section>

<section class="panel abs" style="left:49px;top:432px;width:124px;height:372px">
  <div class="panel-head head-green">Your Favourite</div>
  <div class="person"><div class="thumb" role="img" aria-label="Favourite member photo" style="background:linear-gradient(135deg,#c9c3b4,#7d6e55)"></div><div class="person-info"><b>Person Name</b><br>Age Years<br>City/Location</div></div>
  <div class="person"><div class="thumb" role="img" aria-label="Favourite member photo" style="background:linear-gradient(135deg,#3a2e2a,#c79b74)"></div><div class="person-info"><b>Person Name</b><br>Age Years<br>City/Location</div></div>
  <div class="person"><div class="thumb" role="img" aria-label="Favourite member photo" style="background:linear-gradient(135deg,#e8e4de,#a7684a)"></div><div class="person-info"><b>Person Name</b><br>Age Years<br>City/Location</div></div>
  <div class="person"><div class="thumb" role="img" aria-label="Favourite member photo" style="background:linear-gradient(135deg,#d9d6d2,#9b5a3d)"></div><div class="person-info"><b>Person Name</b><br>Age Years<br>City/Location</div></div>
  <div class="person"><div class="thumb" role="img" aria-label="Favourite member photo" style="background:linear-gradient(135deg,#cfcfcf,#8c7a6c)"></div><div class="person-info"><b>Person Name</b><br>Age Years<br>City/Location</div></div>
  <div class="person"><div class="thumb" role="img" aria-label="Favourite member photo" style="background:linear-gradient(135deg,#5a4a3f,#c79b7d)"></div><div class="person-info"><b>Person Name</b><br>Age Years<br>City/Location</div></div>
</section>

<!-- feed -->
<article class="post abs" style="top:78px"><div class="post-head head-pink">Nunc porta convallis</div><div class="post-body"><div class="avatar" role="img" aria-label="Member photo" style="background:linear-gradient(135deg,#2b2220,#c89b7e)"></div><div class="post-text">Porttitor, g, purus nisi eleifend libero, a tempus libero lectus feugiat<br>felis. Morbi diam mauris, viverra in, gravida eu, mattis in.<div class="post-meta"><span class="bubble"></span>Posted 2 hours ago</div></div></div></article>
<article class="post abs" style="top:187px"><div class="post-head head-pink">Vivamus porttitor g urus</div><div class="post-body"><div class="avatar" role="img" aria-label="Member photo" style="background:linear-gradient(135deg,#b8402a,#f0cdb5 60%,#1d3c6a)"></div><div class="post-text">Porttitor, g, purus nisi eleifend libero, a tempus libero lectus feugiat<br>felis. Morbi diam mauris, viverra in, gravida eu, mattis in.<div class="post-meta"><span class="bubble"></span>Posted 2 hours ago</div></div></div></article>
<article class="post abs" style="top:294px"><div class="post-head head-green">Class aptent taciti</div><div class="post-body"><div class="avatar" role="img" aria-label="Member photo" style="background:linear-gradient(135deg,#5a4030,#e2b394)"></div><div class="post-text">Porttitor, g, purus nisi eleifend libero, a tempus libero lectus feugiat<br>felis. Morbi diam mauris, viverra in, gravida eu, mattis in.<div class="post-meta"><span class="bubble"></span>Posted 2 hours ago</div></div></div></article>
<article class="post abs" style="top:403px"><div class="post-head head-orange">Etiam est unc venenatis</div><div class="post-body"><div class="avatar" role="img" aria-label="Member photo" style="background:linear-gradient(135deg,#2a1c18,#e8c4ad)"></div><div class="post-text">Porttitor, g, purus nisi eleifend libero, a tempus libero lectus feugiat<br>felis. Morbi diam mauris, viverra in, gravida eu, mattis in.<div class="post-meta"><span class="bubble"></span>Posted 2 hours ago</div></div></div></article>
<article class="post abs" style="top:510px"><div class="post-head head-orange">Phasellus felis dolor scelerisque</div><div class="post-body"><div class="avatar" role="img" aria-label="Member photo" style="background:linear-gradient(135deg,#2b2420,#b5835f)"></div><div class="post-text">Porttitor, g, purus nisi eleifend libero, a tempus libero lectus feugiat<br>felis. Morbi diam mauris, viverra in, gravida eu, mattis in.<div class="post-meta"><span class="bubble"></span>Posted 2 hours ago</div></div></div></article>
<article class="post abs" style="top:619px"><div class="post-head head-pink">Class aptent taciti sociosqu</div><div class="post-body"><div class="avatar" role="img" aria-label="Member photo" style="background:linear-gradient(135deg,#5b4a30,#d8b08a)"></div><div class="post-text">Porttitor, g, purus nisi eleifend libero, a tempus libero lectus feugiat<br>felis. Morbi diam mauris, viverra in, gravida eu, mattis in.<div class="post-meta"><span class="bubble"></span>Posted 2 hours ago</div></div></div></article>
<article class="post abs" style="top:725px;left:189px"><div class="post-head head-blue">Nunc porta convallis ped</div><div class="post-body"><div class="avatar" role="img" aria-label="Member photo" style="background:linear-gradient(135deg,#e6e8ea,#b58a70 60%,#3c2a22)"></div><div class="post-text">Porttitor, g, purus nisi eleifend libero, a tempus libero lectus feugiat<br>felis. Morbi diam mauris, viverra in, gravida eu, mattis in.<div class="post-meta"><span class="bubble"></span>Posted 2 hours ago</div></div></div></article>
<article class="post abs" style="top:834px;left:189px"><div class="post-head head-green">Duis sed tellus et</div><div class="post-body"><div class="avatar" role="img" aria-label="Member photo" style="background:linear-gradient(135deg,#3e5a2e,#d2a888)"></div><div class="post-text">Porttitor, g, purus nisi eleifend libero, a tempus libero lectus feugiat<br>felis. Morbi diam mauris, viverra in, gravida eu, mattis in.<div class="post-meta"><span class="bubble"></span>Posted 2 hours ago</div></div></div></article>

<div class="pager abs"><span>View more comments</span><div class="pages"><span class="current">1</span><span>2</span><span>3</span><span>4</span><span>5</span><span>7</span></div></div>

<!-- right column -->
<aside class="beta abs"><strong>Website Our Site</strong><span>is Currently Free During Beta Testing.</span></aside>

<section class="panel abs" style="left:534px;top:162px;width:124px;height:294px">
  <div class="panel-head head-blue">Your Matches</div>
  <ul class="match-list">
    <li>Phasellus felis dolor scelerisq</li><li>Tempus eget lobortis</li><li>Donec scelerisque leo</li><li>Praesent sit amet est.</li><li>In dictum dolor eu dictum</li><li>Porttitor enim felis viverra</li><li>Luctus massa purus</li><li>Etiam nulla massa</li>
  </ul>
  <div class="tile-grid">
    <div class="tile" role="img" aria-label="Match photo" style="background:#8a6a4a"></div>
    <div class="tile" role="img" aria-label="Match photo" style="background:#3a3330"></div>
    <div class="tile" role="img" aria-label="Match photo" style="background:#9cc07a"></div>
    <div class="tile" role="img" aria-label="Match photo" style="background:#a07a5e"></div>
    <div class="tile" role="img" aria-label="Match photo" style="background:#7a98b0"></div>
    <div class="tile" role="img" aria-label="Match photo" style="background:#6a4a32"></div>
    <div class="tile" role="img" aria-label="Match photo" style="background:#4a4a4a"></div>
    <div class="tile" role="img" aria-label="Match photo" style="background:#5e6a3a"></div>
    <div class="tile" role="img" aria-label="Match photo" style="background:#d8b8b0"></div>
  </div>
</section>

<section class="panel abs" style="left:534px;top:465px;width:124px;height:157px">
  <div class="panel-head head-orange">Background Select</div>
  <div class="tile-grid">
    <div class="tile" role="img" aria-label="Sand texture background" style="background:#b89a5a"></div>
    <div class="tile" role="img" aria-label="Strawberry background" style="background:#c8302a"></div>
    <div class="tile" role="img" aria-label="Blue tech background" style="background:linear-gradient(135deg,#1a5e9a,#6ab8e0)"></div>
    <div class="tile" role="img" aria-label="Lime pattern background" style="background:#b8de8a"></div>
    <div class="tile" role="img" aria-label="Pink pattern background" style="background:#ea6e98"></div>
    <div class="tile" role="img" aria-label="Deep blue background" style="background:#1450a8"></div>
    <div class="tile" role="img" aria-label="Dotted pattern background" style="background:linear-gradient(135deg,#3a1a3a,#d85aa0)"></div>
    <div class="tile" role="img" aria-label="Pastel stripes background" style="background:linear-gradient(90deg,#f4a4c0,#f8e48a,#8ad4d8)"></div>
    <div class="tile" role="img" aria-label="Orange swirl background" style="background:linear-gradient(135deg,#f4a450,#c85a1a)"></div>
  </div>
</section>

<!-- footer -->
<footer class="site-footer abs">
  <div class="footer-col abs" style="left:78px"><h3>About Us</h3><ul><li>Phasellus felis</li><li>Dolor scelerisque</li><li>Rempus eget</li><li>lobortis id libero</li><li>Vivamus porttitor</li></ul></div>
  <span class="divider abs" style="left:164px"></span>
  <div class="footer-col abs" style="left:189px"><h3>Features</h3><ul><li>Phasellus felis</li><li>Rempus eget</li><li>lobortis id libero</li><li>Vivamus porttitor</li></ul></div>
  <span class="divider abs" style="left:274px"></span>
  <div class="footer-col abs" style="left:304px"><h3>Support</h3><ul><li>Phasellus felis</li><li>Dolor scelerisque</li><li>Rempus</li><li>Vivamus porttitor</li></ul></div>
  <span class="divider abs" style="left:387px"></span>
  <div class="footer-col abs" style="left:414px"><h3>Term of Use</h3><ul><li>Dolor scelerisque</li><li>Rempus eget</li><li>lobortis id libero</li><li>Vivamus porttitor</li></ul></div>
  <span class="divider abs" style="left:514px"></span>
  <div class="footer-col abs" style="left:542px"><h3>Get In Touch</h3>
    <div class="social"><span style="background:#3b5998"></span><span style="background:#3fb6e8"></span><span style="background:#1a6ea8"></span><span style="background:#f28a1a"></span></div>
  </div>
  <div class="footer-brand abs">winkatwheel<span class="brand-dot"></span></div>
  <div class="footer-base abs">© 2013 Company Name. All right reserved. Term of Use</div>
</footer>

</body>
</html>
```